Construction material supplies company business card ****

1. Full company name “K T Masonry Works Ltd”
I am after a Business card design for the company as a whole. We are better known in Solomon Islands as “K T Masonry” for short.

We are a building materials supplier of
Ready Mixed Concrete, Bricks and Blocks,
Quarry products- gravel, aggregates, sand etc.
Cement distributor/retailer of reputable brands.
Other prefab concrete products. Culverts, wave breakers, concrete retaining blocks etc.

2. Competitive Advantage over Competition: Quality, efficient, professional, dependable, reliable

3. We want people to feel trust worthy, high quality, strong when they see our brand

5. No preference to color. Maybe more sturdy and corporate. Not fancy.

Industry/Entity Type

CONSTRUCTION SUPPLY

Contact Information for Business Card

Name, Position, office phone mob phone, email

Requirements
Must have
• the company logo
Nice to have
• would like to see a mixture of designs, of with logo only and also with simple graphic designs to bring out the company whilst still have the strong sturdy professional feeling

```html
<!DOCTYPE html>
<html lang="en">
<head>
<meta charset="utf-8">
<title>K T Masonry — Business Card</title>
<link rel="stylesheet" href="https://fonts.googleapis.com/css2?family=Raleway:wght@400;700;800&family=Arimo:wght@400&display=swap">
<style>
  :root {
    --navy: #15426b;
    --navy-deep: #123a5f;
    --ink: #111111;
    --grey: #6b6b6b;
    --paper: #ffffff;
    --backdrop: #e9ebee;
  }
  * { margin: 0; padding: 0; box-sizing: border-box; }
  html, body { width: 1200px; height: 900px; overflow: hidden; }
  body {
    background: var(--backdrop);
    position: relative;
    font-family: "Arimo", Arial, sans-serif;
  }
  .card {
    position: absolute;
    left: 250px;
    width: 700px;
    height: 400px;
    overflow: hidden;
    box-shadow: 0 6px 18px rgba(0,0,0,0.18);
  }
  /* Front side */
  .card--front {
    top: 40px;
    background: var(--navy);
    display: flex;
    align-items: center;
    justify-content: center;
  }
  .brand-front {
    display: flex;
    align-items: center;
    gap: 18px;
    color: var(--paper);
    font-family: "Raleway", sans-serif;
    font-weight: 800;
    font-size: 62px;
    letter-spacing: 4px;
    text-transform: uppercase;
  }
  .brand-square {
    width: 34px;
    height: 34px;
    background: currentColor;
  }
  /* Back side */
  .card--back {
    top: 470px;
    background: var(--paper);
  }
  .brand-back {
    position: absolute;
    left: 36px;
    top: 42px;
    display: flex;
    align-items: center;
    gap: 14px;
    color: var(--navy);
    font-family: "Raleway", sans-serif;
    font-weight: 800;
    font-size: 40px;
    letter-spacing: 3px;
    text-transform: uppercase;
  }
  .brand-back .brand-square { width: 24px; height: 24px; }
  .holder {
    position: absolute;
    left: 0;
    top: 196px;
    padding-left: 34px;
  }
  .holder__tab {
    position: absolute;
    left: 0;
    top: 2px;
    width: 10px;
    height: 50px;
    background: var(--navy);
    border-radius: 0 4px 4px 0;
  }
  .holder__name {
    font-family: "Raleway", sans-serif;
    font-weight: 700;
    font-size: 25px;
    color: var(--navy);
  }
  .holder__role {
    font-family: "Raleway", sans-serif;
    font-size: 13px;
    color: var(--grey);
    margin-top: 2px;
  }
  .contacts {
    position: absolute;
    left: 40px;
    top: 268px;
    list-style: none;
  }
  .contacts li {
    display: flex;
    align-items: center;
    gap: 22px;
    height: 24px;
    font-size: 17px;
    color: var(--ink);
  }
  .contacts svg { width: 16px; height: 16px; fill: var(--navy); flex: none; }
  .footer-bands {
    position: absolute;
    left: 0;
    bottom: 0;
    width: 700px;
    height: 80px;
  }
</style>
</head>
<body>

  <section class="card card--front">
    <div class="brand-front">
      <span class="brand-square"></span>
      <span>K T Masonry</span>
    </div>
  </section>

  <section class="card card--back">
    <div class="brand-back">
      <span class="brand-square"></span>
      <span>K T Masonry</span>
    </div>

    <div class="holder">
      <span class="holder__tab"></span>
      <div class="holder__name">Peter Malasa</div>
      <div class="holder__role">Director</div>
    </div>

    <ul class="contacts">
      <li>
        <svg viewBox="0 0 24 24" aria-hidden="true"><path d="M6.6 10.8a15.1 15.1 0 0 0 6.6 6.6l2.2-2.2a1 1 0 0 1 1-.25 11.4 11.4 0 0 0 3.6.57 1 1 0 0 1 1 1V20a1 1 0 0 1-1 1A17 17 0 0 1 3 4a1 1 0 0 1 1-1h3.5a1 1 0 0 1 1 1c0 1.25.2 2.45.57 3.57a1 1 0 0 1-.25 1z"/></svg>
        <span>677 202 4150</span>
      </li>
      <li>
        <svg viewBox="0 0 24 24" aria-hidden="true"><path d="M7 1h10a2 2 0 0 1 2 2v18a2 2 0 0 1-2 2H7a2 2 0 0 1-2-2V3a2 2 0 0 1 2-2zm0 3v14h10V4zm5 15.2a1.2 1.2 0 1 0 0 2.4 1.2 1.2 0 0 0 0-2.4z"/></svg>
        <span>677 748 3391</span>
      </li>
      <li>
        <svg viewBox="0 0 24 24" aria-hidden="true"><path d="M2 5h20v14H2zm2 2v.5l8 5 8-5V7zm0 2.8V17h16V9.8l-8 5z"/></svg>
        <span>info@ktmasonry.com</span>
      </li>
      <li>
        <svg viewBox="0 0 24 24" aria-hidden="true"><path d="M12 2a10 10 0 1 0 0 20 10 10 0 0 0 0-20zm-1 17.9A8 8 0 0 1 4.1 11H7a15 15 0 0 0 4 8.9zM4.1 9A8 8 0 0 1 11 4.1 15 15 0 0 0 7 9zm8.9 10.9A15 15 0 0 0 17 11h2.9a8 8 0 0 1-6.9 8.9zM17 9a15 15 0 0 0-4-4.9A8 8 0 0 1 19.9 9z"/></svg>
        <span>www.ktmasonry.com</span>
      </li>
    </ul>

    <svg class="footer-bands" viewBox="0 0 700 80" aria-hidden="true">
      <polygon points="0,52 468,52 476,44 0,44" fill="var(--ink)"/>
      <polygon points="0,80 700,80 700,0 486,0 476,14 476,62 0,62" fill="var(--navy)"/>
    </svg>
  </section>

</body>
</html>
```